Marvane Pour Over Coffee Filter Packaging Design

We are a brand new company starting to sell coffee related products. The coffee filter that we are about to sell will be copper color. We are working on the exact product picture, but a temporary one will be in uploaded files.We want the box to be simple, yet elegant and not too flashy. We prefer black, rose gold, white design, but are open to other designs. The uploaded files are just samples of what we like. "Marvane" means "owl" in French, we want an owl to be on the logo. Coffee related logo design is best, but we are open to other ideas. Size of this particular packaging is 14x14x12 cm

Target Market(s)

Online Retail

Industry/Entity Type

It Company

Logo Text

"Marvane Products" and "Marvane"

Other font styles liked:
• Your choice

Colors

Designer to choose colors to be used in the design.

Requirements
Must have
• Owl on the logo. Product description in a word file attached.
Nice to have
• Read product description

```html
<!DOCTYPE html>
<html lang="en">
<head>
<meta charset="utf-8">
<title>Marvane Pour Over Coffee Filter – Packaging</title>
<link href="https://fonts.googleapis.com/css2?family=Michroma&family=Montserrat:wght@400;600;700&display=swap" rel="stylesheet">
<style>
  :root {
    --page-bg: #f1f1f1;
    --side-bg: #f7f7f7;
    --front-bg-light: #b9babc;
    --front-bg-dark: #9fa1a3;
    --ink: #2b2b2b;
    --ink-soft: #4a4a4a;
    --title-grey: #4d4e50;
    --gold-light: #f3dfae;
    --gold-mid: #cfae6d;
    --gold-dark: #8e6f3a;
    --grounds-light: #8a5a3c;
    --grounds-dark: #3b2116;
    --icon-grey: #8c8d8f;
  }
  * { box-sizing: border-box; margin: 0; padding: 0; }
  html, body { width: 1200px; height: 1200px; overflow: hidden; }
  body {
    background: var(--page-bg);
    font-family: "Montserrat", sans-serif;
    color: var(--ink);
  }
  .package {
    position: absolute;
    left: 80px; top: 230px;
    width: 1040px; height: 740px;
    display: flex;
    box-shadow: 0 20px 50px rgba(0,0,0,0.12);
  }
  /* Side panel */
  .side-panel {
    width: 420px; height: 100%;
    background: var(--side-bg);
    padding: 46px 40px 30px 40px;
    position: relative;
  }
  .tips-title {
    font-family: "Michroma", sans-serif;
    font-size: 26px;
    line-height: 1.2;
    letter-spacing: 1px;
    color: #111;
    margin-bottom: 18px;
  }
  .tips-text {
    font-size: 13.5px;
    line-height: 1.45;
    color: var(--ink-soft);
    margin-bottom: 14px;
  }
  .roast-block {
    display: flex;
    gap: 14px;
    margin-bottom: 14px;
  }
  .grounds-photo {
    width: 110px; height: 150px;
    flex-shrink: 0;
    margin-left: -40px;
    background: radial-gradient(ellipse at 45% 40%, var(--grounds-light), var(--grounds-dark) 70%, transparent 72%);
  }
  .roast-notes { text-align: center; }
  .tips-highlight {
    font-size: 13.5px;
    font-weight: 700;
    line-height: 1.35;
    color: #1e1e1e;
    margin-bottom: 14px;
  }
  .social-row {
    position: absolute;
    left: 40px; bottom: 34px;
    display: flex; gap: 22px;
  }
  .social-square {
    width: 24px; height: 24px;
    background: var(--icon-grey);
  }
  /* Front panel */
  .front-panel {
    flex: 1; height: 100%;
    position: relative;
    overflow: hidden;
    background: linear-gradient(120deg, var(--front-bg-light), var(--front-bg-dark));
  }
  .brand-mark {
    position: absolute;
    left: 58px; top: 42px;
    display: flex; flex-direction: column; align-items: center; gap: 14px;
  }
  .brand-dot {
    width: 70px; height: 70px;
    border-radius: 50%;
    border: 2px solid var(--title-grey);
  }
  .brand-name {
    font-family: "Montserrat", sans-serif;
    font-weight: 600;
    font-size: 20px;
    color: var(--title-grey);
    letter-spacing: 0.5px;
  }
  .product-title {
    position: absolute;
    left: 40px; top: 410px;
    font-family: "Michroma", sans-serif;
    color: var(--title-grey);
  }
  .product-title .kicker {
    display: block;
    font-size: 15px;
    letter-spacing: 1px;
    margin-bottom: 6px;
  }
  .product-title .main {
    display: block;
    font-size: 54px;
    line-height: 1.12;
    letter-spacing: 2px;
  }
  .product-photo {
    position: absolute;
    left: 260px; top: 40px;
    width: 420px; height: 640px;
    background:
      radial-gradient(ellipse 70% 12% at 55% 12%, var(--gold-light), transparent 70%),
      linear-gradient(180deg, var(--gold-mid), var(--gold-light) 45%, var(--gold-mid) 75%, var(--gold-dark));
    clip-path: polygon(0 6%, 100% 0, 100% 100%, 45% 100%, 10% 96%, 30% 80%);
  }
</style>
</head>
<body>
  <main class="package">
    <section class="side-panel">
      <h2 class="tips-title">TIPS AND<br>TRICKS</h2>
      <p class="tips-text">To make the best cup of coffee, make sure your grind it not too coarse and not too fine, it has to be just right! We generally recommend a medium-coarse grind to achieve the best results.</p>
      <div class="roast-block">
        <div class="grounds-photo" role="img" aria-label="Pile of ground coffee"></div>
        <div class="roast-notes">
          <p class="tips-highlight">The darker the roast of your coffee the more “spicy” and bittersweet it will taste.</p>
          <p class="tips-highlight">Light roasts retain most of the caffeine from the coffee bean</p>
        </div>
      </div>
      <p class="tips-text">The optimum temperature for pour over coffee water is 185 to 205 degrees Fahrenheit. You can find it's easy to achieve this by bringing your water to a boil and then letting it sit for about 30 seconds to minute.</p>
      <p class="tips-text">Pre-infusion: this is a very important step when using a pour over coffee filter. Pour just enough water onto coffee to allow water to soak through the grounds. Give it a minute or so before brewing your coffee.<br>We recommend keeping the spout of the kettle as close to the brew bed as possible, pouring onto — not through — the coffee bed. After pre-infusion, pour softly in a circular pattern.</p>
      <div class="social-row" aria-label="Social links">
        <span class="social-square"></span>
        <span class="social-square"></span>
        <span class="social-square"></span>
        <span class="social-square"></span>
        <span class="social-square"></span>
      </div>
    </section>
    <section class="front-panel">
      <div class="brand-mark">
        <span class="brand-dot"></span>
        <span class="brand-name">Marvane</span>
      </div>
      <h1 class="product-title">
        <span class="kicker">HIGH QUALITY</span>
        <span class="main">COFFEE<br>FILTER</span>
      </h1>
      <div class="product-photo" role="img" aria-label="Gold stainless steel mesh pour over coffee filter cone with stand"></div>
    </section>
  </main>
</body>
</html>
```